Zielgruppe
Ich biete Farbtupferei, Glitzertattoos, Schwangerschaftsbemalung (Belly-Painting), Wunden schminken, Vermietung von einer Popcornmaschine.
Aufgabenstellung
Mein Anliegen betrifft hiermit die Gestaltung einer Website.
In Bezug auf die Website gibt es schon eine gekaufte Domain, welche lautet: frau-pinselmaus.de und kann über VERAX eingerichtet werden.
Auf dieser WEBSITE soll sich folgendes Menü befinden:
- Anfrage stellen/Angebot einholen mit zusätzlicher Frage 'Wie sind Sie auf mich aufmerksam geworden?'
Mit einem Feld für den Namen, E-Mail, Telefonnummer, Gewünschtes Datum.
Sowie die Frage 'Wie sind Sie auf mich aufmerksam geworden?' (zum Ankreuzen) Freunde, Empfehlung, Flyer, soziale medienoder sonstiges.
Gerne auch zum ankreuzen welche Leistung Sie möchten. Farbtupferei, Glitzer Tattoos, Schwangerschaftsbemalung, oder Popcornmaschiene. (So brauchen haben es die Kunden einfacher nur anzukreuzen und ich sehe gleich worum es sich handelt.)
- eine Leistungsübersicht: Farbtupferei, Glitzertattoos, Schwangerschaftsbemalung (Belly-Painting), Wunden schminken, Vermietung von einer Popcornmaschine
- meine Kontaktdaten
- Galerie (es kann eine Auswahl der angehängten Bilder sein)
!!! mein Wunsch wäre, dass sich die Figur von dem Logo in verschiedenen Positionen auf der Website an das Menü angepasst wiederfindet (wenn dies irgendwie machbar ist)
z.B. meine Figur (Logo) stehend am Rand oder liegend.....
- erwünscht ist auch eine Verknüpfung mit einem Findlaeintrag
- Hinweis auf Kontaktor und Lumoravue (bin gerade dabei ein öffentliches Profil dort zu erstellen)
!Wichtig wäre die nötige Einstellung, damit die Website sowohl in der mobilen Version als auch der PC-Version mit ALLEN oben genannten Informationen dargestellt wird!
Dankbar wäre ich noch für die Information, ob für mich laufende Kosten (monatlich oder jährlich) für die Website entstehen?
Mein Logo ist mir sehr wichtig und sollte gut sichtbar und erkennbar sein auch die Schriftart kann auf der Website aufgegriffen werden

```html
<!DOCTYPE html>
<html lang="de">
<head>
<meta charset="utf-8">
<title>Frau Pinselmaus – Farbtupferei &amp; Glitzer Tattoos</title>
<link href="https://fonts.googleapis.com/css2?family=Amatic+SC:wght@400;700&family=Poppins:wght@300;400;600&display=swap" rel="stylesheet">
<style>
:root{
  --teal:#1e9fae;
  --teal-deep:#3ab2bf;
  --mist:#e8f5f7;
  --white:#ffffff;
  --ink:#1a1a1a;
  --orange:#f07f3c;
  --card-line:#ef8a4e;
}
*{margin:0;padding:0;box-sizing:border-box}
html,body{width:1200px;height:5273px;overflow:hidden}
body{font-family:"Poppins",sans-serif;color:var(--ink);position:relative;
  background:linear-gradient(180deg,#ffffff 0px,#eef7f8 700px,#e2f2f4 1400px,#d2ecef 2500px,#a6dbe1 3300px,#6cc4cd 4100px,var(--teal-deep) 4829px,var(--white) 4829px)}
.abs{position:absolute}
.display{font-family:"Amatic SC",sans-serif;font-weight:400;line-height:1;letter-spacing:1px;white-space:nowrap}

/* Header */
.brand{display:flex;align-items:center;gap:16px}
.brand-dot{width:30px;height:30px;border-radius:50%;background:var(--teal);flex:none}
.brand-name{font-family:"Amatic SC",sans-serif;font-weight:700;color:var(--teal);line-height:.9;white-space:nowrap}
.site-header .brand{left:41px;top:96px}
.site-header .brand-name{font-size:72px}
.main-nav a{position:absolute;top:130px;font-family:"Amatic SC",sans-serif;font-size:52px;color:var(--teal);text-decoration:none;line-height:1;white-space:nowrap}

/* Leistungen */
.section-title{color:var(--teal)}
.service-photo{position:absolute;border-radius:50%}
.ring-teal{border:6px solid var(--teal)}
.ring-black{border:6px solid var(--ink)}
.service-label{position:absolute;font-weight:600;font-size:28px;text-align:center;line-height:1.5;transform:translateX(-50%);white-space:nowrap}

/* Galerie */
.gallery-tile{position:absolute}

/* Referenzen */
.review{position:absolute;border:3px solid var(--card-line);border-radius:6px;text-align:center;padding:14px 24px;font-size:18px;line-height:1.55;color:var(--ink)}
.stars{display:block;color:var(--white);font-size:20px;letter-spacing:2px;margin-bottom:4px}
.palette-spot{position:absolute;border-radius:50%;background:#f4f4f4;border:4px solid var(--ink)}

/* Kontakt */
.contact-form{position:absolute;left:254px;top:3477px;width:711px;color:var(--white);font-weight:300;font-size:28px}
.field{position:absolute;left:0;width:711px;height:51px;border:2px solid var(--white);border-radius:3px;padding:4px 10px;line-height:40px;color:var(--white)}
.question{position:absolute;left:8px;white-space:nowrap}
.check{position:absolute;display:flex;align-items:center;gap:14px;white-space:nowrap}
.check i{display:block;width:34px;height:34px;border:2px solid var(--white);border-radius:4px}
.submit{position:absolute;left:0;top:1088px;width:711px;height:51px;background:var(--orange);color:var(--white);font-weight:400;font-size:28px;text-align:center;line-height:51px}

/* Footer */
.site-footer .brand{left:41px;top:4985px}
.site-footer .brand-name{font-size:104px}
.footer-contact{position:absolute;right:20px;top:5030px;text-align:right;color:var(--teal);font-size:29px;line-height:42px;white-space:nowrap}
.social{position:absolute;right:20px;top:5165px;display:flex;gap:18px;font-size:22px;color:var(--teal);font-weight:600}
.social span{display:flex;align-items:center;gap:8px}
.social i{display:block;width:40px;height:40px;background:var(--teal);border-radius:6px}
</style>
</head>
<body>

<header class="site-header">
  <div class="abs brand"><span class="brand-dot"></span><span class="brand-name">Frau<br>Pinselmaus</span></div>
  <nav class="main-nav">
    <a href="#leistungen" style="left:418px">Leistungen</a>
    <a href="#galerie" style="left:653px">Galerie</a>
    <a href="#referenzen" style="left:829px">Referenzen</a>
    <a href="#kontakt" style="right:22px">Kontakt</a>
  </nav>
</header>

<section id="leistungen">
  <h2 class="abs display section-title" style="left:72px;top:405px;font-size:143px">Leistungen</h2>

  <div class="service-photo ring-teal" role="img" aria-label="Foto: bemalter Babybauch" style="left:72px;top:619px;width:278px;height:278px;background:radial-gradient(circle,#c9c9c9,#5a5a5a)"></div>
  <div class="service-photo ring-black" role="img" aria-label="Foto: Belly Painting Detail" style="left:270px;top:598px;width:144px;height:144px;background:radial-gradient(circle,#d9cfc2,#6b5f55)"></div>
  <div class="service-label" style="left:196px;top:912px">Belly Painting</div>

  <div class="service-label" style="left:836px;top:500px">Verleih<br>Popcornmaschine</div>
  <div class="service-photo ring-black" role="img" aria-label="Foto: Popcorntüten" style="left:690px;top:600px;width:274px;height:274px;background:radial-gradient(circle,#f2e3d6,#c63a3f)"></div>

  <div class="service-photo ring-black" role="img" aria-label="Foto: Glitzertattoos auf Handgelenken" style="left:406px;top:832px;width:278px;height:278px;background:radial-gradient(circle,#c8b39c,#7a6450)"></div>
  <div class="service-label" style="left:537px;top:1128px">Glitzertattoos</div>

  <div class="service-photo ring-teal" role="img" aria-label="Foto: Farbtupferei beim Schminken eines Kindes" style="left:744px;top:916px;width:270px;height:270px;background:radial-gradient(circle,#b7c4b9,#3c4a44)"></div>
  <div class="service-label" style="left:891px;top:1202px">Farbtupferei</div>

  <div class="service-photo ring-teal" role="img" aria-label="Foto: geschminkte Wunde im Gesicht" style="left:70px;top:991px;width:278px;height:278px;background:radial-gradient(circle,#b5473f,#d8c3b6)"></div>
  <div class="service-photo ring-black" role="img" aria-label="Foto: geschminkte Hand" style="left:262px;top:1131px;width:188px;height:188px;background:radial-gradient(circle,#b8aaa2,#1f1f1f)"></div>
  <div class="service-label" style="left:160px;top:1288px">Wunden<br>Schminken</div>
</section>

<section id="galerie">
  <h2 class="abs display section-title" style="right:58px;top:1325px;font-size:140px">Galerie</h2>
  <div class="gallery-tile" role="img" aria-label="Foto: Belly Painting mit Strohhut" style="left:43px;top:1515px;width:368px;height:316px;background:linear-gradient(160deg,#3f5a2c,#c9b89a)"></div>
  <div class="gallery-tile" role="img" aria-label="Foto: Glitzertattoo wird aufgetragen" style="left:415px;top:1515px;width:366px;height:316px;background:linear-gradient(160deg,#d8a3b4,#6c5350)"></div>
  <div class="gallery-tile" role="img" aria-label="Foto: Bodypainting mit zwei Frauen" style="left:785px;top:1515px;width:368px;height:316px;background:linear-gradient(160deg,#8a5a36,#2d6ea8)"></div>
  <div class="gallery-tile" role="img" aria-label="Foto: Gruppe mit Wunden-Schminke" style="left:43px;top:1835px;width:368px;height:332px;background:linear-gradient(160deg,#8f8a7d,#3a3f4a)"></div>
  <div class="gallery-tile" role="img" aria-label="Foto: Glitzertattoo auf dem Arm" style="left:415px;top:1835px;width:366px;height:332px;background:linear-gradient(160deg,#b8a07f,#d68fb0)"></div>
  <div class="gallery-tile" role="img" aria-label="Foto: geschminkte Hand mit Schnittwunden" style="left:785px;top:1835px;width:368px;height:332px;background:linear-gradient(160deg,#2a2a2a,#c79a8f)"></div>
  <div class="gallery-tile" role="img" aria-label="Foto: Farbtupferei am Kindergesicht" style="left:48px;top:2171px;width:363px;height:332px;background:linear-gradient(160deg,#d9cbbf,#2b2b2b)"></div>
  <div class="gallery-tile" role="img" aria-label="Foto: Bodypainting in Arbeit" style="left:415px;top:2171px;width:366px;height:332px;background:linear-gradient(160deg,#8a6a45,#3b82b5)"></div>
  <div class="gallery-tile" role="img" aria-label="Foto: Kindergesicht mit Bienenmotiv" style="left:791px;top:2171px;width:362px;height:332px;background:linear-gradient(160deg,#e9c2a8,#e06a2a)"></div>
</section>

<section id="referenzen">
  <h2 class="abs display" style="left:0;width:1200px;text-align:center;top:2590px;font-size:150px;color:var(--white)">Referenzen</h2>
  <div class="review" style="left:84px;top:2767px;width:494px;height:115px"><span class="stars">★★★★★</span>Alles Bestens, würde ich wieder buchen!</div>
  <div class="review" style="left:608px;top:2767px;width:494px;height:115px"><span class="stars">★★★★★</span>Ich kann nichts sagen außer, super!</div>
  <div class="review" style="left:84px;top:2894px;width:490px;height:203px"><span class="stars">★★★★★</span>So freundlich zu den kleinen. Habe Sie zu einem Kindergeburtstag meiner Tochter gebucht und diese war begeistert. Wirklich zu empfehlen.</div>
  <div class="review" style="left:610px;top:2894px;width:486px;height:203px"><span class="stars">★★★★★</span>Die Kids sind super auf die Popcornmaschine abgefahren.<br>War der Hit der Feier!</div>
  <div class="palette-spot" role="img" aria-label="Illustration: Farbpalette" style="left:1048px;top:2720px;width:94px;height:86px"></div>
  <div class="palette-spot" role="img" aria-label="Illustration: Farbpalette" style="left:48px;top:3045px;width:96px;height:90px"></div>
</section>

<section id="kontakt">
  <h2 class="abs display" style="left:0;width:1200px;text-align:center;top:3175px;font-size:156px;color:var(--white)">Interesse geweckt?</h2>
  <h2 class="abs display" style="left:0;width:1200px;text-align:center;top:3330px;font-size:132px;color:var(--white)">Kontakt</h2>

  <form class="contact-form">
    <div class="field" style="top:0">Name</div>
    <div class="field" style="top:74px">E-Mail Adresse</div>
    <div class="field" style="top:158px">Gewünschtes Datum</div>
    <div class="question" style="top:236px">Welche Leistung wollen Sie in Anspruch nehmen?</div>
    <label class="check" style="left:0;top:287px"><i></i>Farbtupferei</label>
    <label class="check" style="left:0;top:338px"><i></i>Glitzertattoos</label>
    <label class="check" style="left:0;top:391px"><i></i>Popcornmaschine mieten</label>
    <label class="check" style="left:0;top:451px"><i></i>Sonstiges</label>
    <div class="question" style="top:506px">Wie sind Sie auf mich aufmerksam geworden?</div>
    <label class="check" style="left:0;top:557px"><i></i>Freunde</label>
    <label class="check" style="left:202px;top:557px"><i></i>Sozial Media</label>
    <label class="check" style="left:456px;top:557px"><i></i>Empfehlung</label>
    <label class="check" style="left:0;top:614px"><i></i>Sonstiges</label>
    <div class="field" style="top:695px;height:358px;line-height:36px">Ihre Nachricht</div>
    <div class="submit">Absenden</div>
  </form>
</section>

<footer class="site-footer">
  <div class="abs brand"><span class="brand-dot"></span><span class="brand-name">Frau<br>Pinselmaus</span></div>
  <address class="footer-contact" style="font-style:normal">
    Mia Musterfrau<br>
    Telefon: 0471 55382910<br>
    Email: hallo@postfach-beispiel.de
  </address>
  <div class="social">
    <span><i></i>Kontaktor</span>
    <span><i></i>Lumoravue</span>
  </div>
</footer>

</body>
</html>
```